Provide bookkeeping and accounting services to small and growing businesses

We need website and logo design using the name Dornaby as the logo.
The target audience are small companies and startups who need:
1) Simple bookkeeping services
2) Accounting advice that only someone with many years of senior financial experience as a CPA can provide.

The services are provided by two individuals. each of whom specialize in one of the areas.

We want the website to be clean without a lot of visual distraction but don't know how to make a boring subject interesting. We believe our potential clients, small business owners, need to find what they want quickly and easily without a lot of verbiage or distractions.

We've attached a draft of the homepage and have completed the text on most of the other pages.

Target Market(s)

small and early stage growth companies in San Diego North County

Industry/Entity Type

Accounting

Number of Pages Required

1 page

Font styles to use
Sans Serif

Colors
86cfc6
33b8a4
85cae6

Requirements
Must have
• We need a design for the website homepage that includes the name Dornaby as the logo. Must include a design for the name.
• Must have color in teal or greenish blue.
Nice to have
• White background, clean, clear, uncluttered.
• We would like to use the design in a Theme on a WordPress website. Themes Paper Lantern and Quiet Harbour are appealing to us.
Should not have
• Moving pictures

```html
<!DOCTYPE html>
<html lang="en">
<head>
<meta charset="utf-8">
<title>Dornaby Accounting &amp; Bookkeeping</title>
<link href="https://fonts.googleapis.com/css2?family=Open+Sans:wght@400;600;700&family=Roboto:wght@300;400&family=Roboto+Condensed:wght@700&display=swap" rel="stylesheet">
<style>
:root{
  --teal:#33b8a4;
  --teal-soft:#86cfc6;
  --ink:#444a4f;
  --text:#555b60;
  --muted:#7a8085;
  --footer-bg:#f1f2f2;
  --bar-bg:#333639;
  --line:#e1e3e4;
  --white:#ffffff;
}
*{margin:0;padding:0;box-sizing:border-box}
html,body{width:944px;height:1200px;overflow:hidden;background:var(--white)}
body{position:relative;font-family:'Open Sans',sans-serif;color:var(--text)}
.abs{position:absolute}

/* header */
.site-header{position:absolute;left:0;top:0;width:944px;height:75px;background:var(--white)}
.brand-dot{left:77px;top:16px;width:43px;height:43px;border-radius:50%;background:var(--teal)}
.brand-name{left:128px;top:15px;font-size:23px;font-weight:700;letter-spacing:1.5px;color:var(--ink);line-height:1}
.brand-tag{left:130px;top:42px;font-size:11px;color:var(--ink);letter-spacing:.3px}
.main-nav a{position:absolute;top:33px;font-size:10.5px;letter-spacing:.8px;color:var(--text);text-decoration:none;text-transform:uppercase}
.main-nav a.active{color:var(--teal)}

/* hero */
.hero{left:0;top:75px;width:944px;height:433px;background:linear-gradient(115deg,#9aa0a6 0%,#c9c4bc 35%,#8c9199 60%,#3f4c62 85%,#1e3266 100%)}
.hero-title{left:480px;top:200px;font-family:'Roboto Condensed',sans-serif;font-weight:700;font-size:31px;line-height:35px;color:var(--white)}
.hero-arrow{top:190px}

/* services */
.section-title{left:0;top:548px;width:944px;text-align:center;font-family:'Roboto',sans-serif;font-weight:400;font-size:32px;color:var(--ink)}
.section-rule{left:443px;top:591px;width:58px;height:1px;background:var(--teal)}
.service{position:absolute;top:624px;width:252px}
.service-icon{position:absolute;left:0;top:2px}
.service-name{position:absolute;left:41px;top:0;font-family:'Roboto',sans-serif;font-size:16px;color:var(--ink);white-space:nowrap}
.service-sub{position:absolute;left:41px;top:20px;font-size:8.5px;color:var(--ink)}
.service-photo{position:absolute;left:0;top:46px;width:251px;height:145px;border:1px solid var(--line);padding:3px;background:var(--white)}
.service-photo div{width:100%;height:100%}
.service-text{position:absolute;left:0;top:206px;width:250px;font-size:8.6px;line-height:16px;color:var(--text)}

/* footer */
.site-footer{left:0;top:930px;width:944px;height:222px;background:var(--footer-bg)}
.foot-dot{left:107px;top:1006px;width:46px;height:46px;border-radius:50%;background:var(--teal)}
.foot-name{left:50px;top:1053px;width:160px;text-align:center;font-size:17px;font-weight:700;letter-spacing:1px;color:var(--ink)}
.foot-tag{left:50px;top:1071px;width:160px;text-align:center;font-size:8px;color:var(--ink)}
.foot-heading{font-family:'Roboto',sans-serif;font-weight:300;font-size:14px;color:var(--ink);text-transform:uppercase}
.newsletter-copy{left:248px;top:1002px;width:206px;font-size:8.4px;line-height:15px;text-align:justify;color:var(--text)}
.field{position:absolute;background:var(--white);border:1px solid #e4e5e6;font-size:8.5px;color:var(--text);padding-left:11px;display:flex;align-items:center}
.subscribe{position:absolute;left:378px;top:1082px;width:77px;height:32px;background:var(--teal);color:var(--white);font-size:10px;display:flex;align-items:center;justify-content:center}
.contact-line{font-size:10px;line-height:16px;color:var(--text)}
.quick-links a{position:absolute;left:790px;font-size:8.6px;color:var(--text);text-decoration:none}
.bottom-bar{left:0;top:1152px;width:944px;height:48px;background:var(--bar-bg);color:#fff;font-size:8.6px;display:flex;align-items:center;justify-content:center}
</style>
</head>
<body>

<header class="site-header">
  <div class="abs brand-dot"></div>
  <div class="abs brand-name">DORNABY</div>
  <div class="abs brand-tag">Accounting &amp; Bookkeeping</div>
  <nav class="main-nav">
    <a class="active" style="left:370px">Home</a>
    <a style="left:437px">About Us</a>
    <a style="left:525px">Services</a>
    <a style="left:608px">Experience</a>
    <a style="left:705px">Resources</a>
    <a style="left:800px">Contact Us</a>
  </nav>
</header>

<section class="abs hero" role="img" aria-label="Photo of a consultant pointing a pen at a tablet beside printed financial charts">
  <h1 class="abs hero-title">DORNABY ACCOUNTING<br>&amp; BOOKKEEPING</h1>
  <svg class="abs hero-arrow" style="left:27px" width="24" height="48" viewBox="0 0 24 48"><polyline points="22,2 2,24 22,46" fill="none" stroke="#ffffff" stroke-opacity=".55" stroke-width="1"/></svg>
  <svg class="abs hero-arrow" style="left:890px" width="24" height="48" viewBox="0 0 24 48"><polyline points="2,2 22,24 2,46" fill="none" stroke="#ffffff" stroke-width="1"/></svg>
</section>

<h2 class="abs section-title">Our Services</h2>
<div class="abs section-rule"></div>

<article class="service" style="left:77px">
  <svg class="service-icon" width="34" height="30" viewBox="0 0 34 30"><rect x="1" y="1" width="32" height="21" rx="2" fill="var(--teal)"/><rect x="4" y="4" width="26" height="15" fill="#fff"/><rect x="14" y="22" width="6" height="4" fill="var(--teal)"/><rect x="9" y="26" width="16" height="3" fill="var(--teal)"/></svg>
  <h3 class="service-name">Book Keeping Services</h3>
  <p class="service-sub">Lorem ipsum dolor sit amet,</p>
  <div class="service-photo"><div role="img" aria-label="Photo of hands working on a tablet with a stylus" style="background:linear-gradient(135deg,#b8cfe0,#e6eef3 45%,#3f6fa8 80%,#c6d6e2)"></div></div>
  <p class="service-text">Lorem ipsum dolor sit amet, consectetur adipisicing elit, sed do eiusmod tempor incididunt ut labore et dolore magna aliqua. Ut enim ad minim veniam,</p>
</article>

<article class="service" style="left:346px">
  <svg class="service-icon" width="28" height="30" viewBox="0 0 28 30"><path d="M10 2h8l-3 6h-2z" fill="var(--teal)"/><path d="M10 9h8c6 5 9 10 9 14 0 4-3 6-6 6H7c-3 0-6-2-6-6 0-4 3-9 9-14z" fill="var(--teal)"/><text x="14" y="25" text-anchor="middle" font-family="Open Sans,sans-serif" font-size="12" fill="#fff">$</text></svg>
  <h3 class="service-name">Financial Planning</h3>
  <p class="service-sub">Lorem ipsum dolor sit amet,</p>
  <div class="service-photo"><div role="img" aria-label="Photo of a hand touching glowing dollar signs over a rising bar chart" style="background:linear-gradient(135deg,#6d7fa8,#4a5c8e 50%,#9aa6c6)"></div></div>
  <p class="service-text">Lorem ipsum dolor sit amet, consectetur adipisicing elit, sed do eiusmod tempor incididunt ut labore et dolore magna aliqua. Ut enim ad minim veniam,</p>
</article>

<article class="service" style="left:615px">
  <svg class="service-icon" width="32" height="28" viewBox="0 0 32 28"><circle cx="7" cy="7" r="4" fill="var(--teal)"/><circle cx="25" cy="7" r="4" fill="var(--teal)"/><circle cx="16" cy="9" r="5" fill="var(--teal)"/><path d="M1 20c0-5 3-8 6-8s4 1 5 2c-2 2-3 4-3 7H1z" fill="var(--teal)"/><path d="M31 20c0-5-3-8-6-8s-4 1-5 2c2 2 3 4 3 7h8z" fill="var(--teal)"/><path d="M8 27c0-7 4-11 8-11s8 4 8 11z" fill="var(--teal)"/></svg>
  <h3 class="service-name">Accounting Advice</h3>
  <p class="service-sub">Lorem ipsum dolor sit amet,</p>
  <div class="service-photo"><div role="img" aria-label="Photo of two advisers reviewing printed charts at a desk" style="background:linear-gradient(135deg,#2e3b55,#b9c7d9 45%,#eef0f2 75%,#d8dde3)"></div></div>
  <p class="service-text">Lorem ipsum dolor sit amet, consectetur adipisicing elit, sed do eiusmod tempor incididunt ut labore et dolore magna aliqua. Ut enim ad minim veniam,</p>
</article>

<footer class="abs site-footer"></footer>
<div class="abs foot-dot"></div>
<div class="abs foot-name">DORNABY</div>
<div class="abs foot-tag">Accounting &amp; Bookkeeping</div>

<h4 class="abs foot-heading" style="left:248px;top:975px">Sign up for newsletter</h4>
<p class="abs newsletter-copy">Excepteur sint occaecat cupidatat non proident, sunt in culpa qui officia deserunt</p>
<div class="field" style="left:248px;top:1041px;width:207px;height:33px">Enter Name</div>
<div class="field" style="left:248px;top:1082px;width:130px;height:32px">Enter Email</div>
<div class="subscribe">SUBSCRIBE</div>

<h4 class="abs foot-heading" style="left:540px;top:975px">Contacts us</h4>
<svg class="abs" style="left:541px;top:1009px" width="10" height="13" viewBox="0 0 10 13"><path d="M5 1a4 4 0 0 1 4 4c0 3-4 7-4 7S1 8 1 5a4 4 0 0 1 4-4z" fill="none" stroke="#b5b9bc" stroke-width="1.2"/><circle cx="5" cy="5" r="1.4" fill="#b5b9bc"/></svg>
<p class="abs contact-line" style="left:561px;top:1006px">Carlsbay, North Coast Region<br>Westland</p>
<svg class="abs" style="left:541px;top:1053px" width="11" height="11" viewBox="0 0 11 11"><path d="M2 1l2 0 1 3-1.5 1c.6 1.3 1.2 1.9 2.5 2.5L7 6l3 1v2c0 1-1 1.5-2 1.3C4.5 9.8 1.2 6.5.7 3 .5 2 1 1 2 1z" fill="#b5b9bc"/></svg>
<p class="abs contact-line" style="left:560px;top:1052px;font-size:11px">Phone: (555) 014-2738</p>
<svg class="abs" style="left:542px;top:1080px" width="10" height="8" viewBox="0 0 10 8"><rect width="10" height="8" fill="#b5b9bc"/><polyline points="0,0 5,4 10,0" fill="none" stroke="#f1f2f2" stroke-width="1"/></svg>
<p class="abs contact-line" style="left:561px;top:1076px">info@dornabyaccounting.com</p>

<h4 class="abs foot-heading" style="left:788px;top:974px">Quick links</h4>
<nav class="quick-links">
  <a style="top:1002px">Home</a>
  <a style="top:1020px">About Us</a>
  <a style="top:1037px">Services</a>
  <a style="top:1055px">Experience</a>
  <a style="top:1072px">Resources</a>
  <a style="top:1090px">Contact Us</a>
</nav>

<div class="abs bottom-bar">©2015 - 2016 Dornaby Accounting &amp; Bookkeeping, All Rights Reserved.</div>

</body>
</html>
```